Basic business card

use my newly created logo - and the phrases (Quicker Analysis Loops & Verified Unit Builds) - and my new email domain / ID - use at conferences / tradeshows

Industry/Entity Type

semiconductor

Contact Information for Business Card

Daniel K Forde, Owner, communicate via Logo - Lower COT - Cost of Test, Accelerated NPI - New Product Introduction, phone +1 555 613 0946, Harlow Ridge, Westland, daniel.forde@qal-vub.com

Font styles to use
Sans Serif

Requirements
Nice to have
• re-use my logo created via Pixel Harbor last August (#7315926)

```html
<!DOCTYPE html>
<html lang="en">
<head>
<meta charset="utf-8">
<title>QAL-VUB Business Card</title>
<link href="https://fonts.googleapis.com/css2?family=Montserrat:wght@400;500;700&display=swap" rel="stylesheet">
<style>
  :root {
    --backdrop-top: #d2d2d2;
    --backdrop-bottom: #a9a9a9;
    --card-white: #ffffff;
    --slate: #4a5872;
    --slate-light: #6f7e9b;
    --slate-dark: #2f3c55;
    --accent-orange: #f39219;
    --accent-sky: #4bbfe6;
    --accent-green: #7cc242;
    --text-light: #ffffff;
  }
  * { box-sizing: border-box; margin: 0; padding: 0; }
  html, body { width: 1200px; height: 788px; overflow: hidden; }
  body {
    background: linear-gradient(180deg, var(--backdrop-top), var(--backdrop-bottom));
    font-family: "Montserrat", sans-serif;
    position: relative;
  }
  .card {
    position: absolute;
    top: 239px;
    width: 540px;
    height: 309px;
    border-radius: 22px;
    overflow: hidden;
    box-shadow: 0 14px 30px rgba(0,0,0,0.28);
  }
  .card-front { left: 40px; background: var(--card-white); }
  .card-back { left: 620px; background: var(--slate); }

  .front-bands { position: absolute; inset: 0; }

  .brand {
    position: absolute;
    display: flex;
    align-items: center;
    gap: 12px;
    font-weight: 700;
    letter-spacing: 2px;
  }
  .brand-mark { display: block; }
  .card-front .brand { left: 92px; top: 62px; font-size: 46px; color: var(--slate); }
  .card-front .brand-mark { width: 18px; height: 18px; background: var(--slate); }
  .card-back .brand { left: 0; right: 0; top: 92px; justify-content: center; font-size: 60px; color: var(--slate-light); }
  .card-back .brand-mark { width: 22px; height: 22px; background: var(--slate-light); }

  .holder {
    position: absolute;
    right: 214px;
    top: 236px;
    text-align: right;
  }
  .holder-name { color: var(--accent-orange); font-weight: 700; font-size: 21px; white-space: nowrap; }
  .holder-role { color: var(--text-light); font-size: 13px; margin-top: 3px; }

  .divider {
    position: absolute; left: 338px; top: 186px;
    width: 1px; height: 88px; background: var(--slate-dark);
  }
  .contacts {
    position: absolute; left: 352px; top: 186px;
    list-style: none; color: var(--text-light); font-size: 11.5px;
  }
  .contacts li { display: flex; align-items: center; gap: 7px; margin-bottom: 10px; white-space: nowrap; }
  .contacts svg { width: 12px; height: 12px; flex: none; }

  .tagline {
    position: absolute; left: 0; right: 0; top: 232px;
    text-align: center; font-size: 14px; font-weight: 500;
    color: var(--text-light); letter-spacing: 0.6px;
  }
  .tagline .hl-sky { color: var(--accent-sky); }
  .tagline .hl-green { color: var(--accent-green); }
</style>
</head>
<body>
  <section class="card card-front">
    <svg class="front-bands" viewBox="0 0 540 309" aria-hidden="true">
      <path d="M20 309 C110 185 330 112 540 78 L540 86 C330 120 124 195 34 309 Z" fill="var(--accent-sky)"/>
      <path d="M34 309 C124 195 330 120 540 86 L540 92 C330 128 132 204 48 309 Z" fill="var(--accent-orange)"/>
      <path d="M56 309 C130 205 335 134 540 100 L540 309 Z" fill="var(--slate)"/>
    </svg>
    <div class="brand"><span class="brand-mark"></span>QAL-VUB</div>
    <div class="holder">
      <div class="holder-name">Daniel K Forde</div>
      <div class="holder-role">Owner</div>
    </div>
    <div class="divider"></div>
    <ul class="contacts">
      <li>
        <svg viewBox="0 0 24 24" aria-hidden="true"><path fill="var(--accent-green)" d="M6.6 10.8a15 15 0 0 0 6.6 6.6l2.2-2.2c.3-.3.7-.4 1-.2 1.1.4 2.3.6 3.6.6.6 0 1 .4 1 1V20c0 .6-.4 1-1 1A17 17 0 0 1 3 4c0-.6.4-1 1-1h3.5c.6 0 1 .4 1 1 0 1.3.2 2.5.6 3.6.1.3 0 .7-.2 1z"/></svg>
        +1 555 613 0946
      </li>
      <li>
        <svg viewBox="0 0 24 24" aria-hidden="true"><rect x="2" y="5" width="20" height="14" rx="1" fill="var(--accent-green)"/><path d="M3 6l9 7 9-7" stroke="var(--slate)" stroke-width="2" fill="none"/></svg>
        daniel.forde@qal-vub.com
      </li>
      <li>
        <svg viewBox="0 0 24 24" aria-hidden="true"><path fill="var(--accent-green)" d="M12 2a7 7 0 0 0-7 7c0 5 7 13 7 13s7-8 7-13a7 7 0 0 0-7-7zm0 9.5A2.5 2.5 0 1 1 12 6.5a2.5 2.5 0 0 1 0 5z"/></svg>
        Harlow Ridge, Westland
      </li>
    </ul>
  </section>

  <section class="card card-back">
    <div class="brand"><span class="brand-mark"></span>QAL-VUB</div>
    <p class="tagline">Quicker <span class="hl-sky">Analysis Loops</span> &amp; Verified <span class="hl-green">Unit Builds</span></p>
  </section>
</body>
</html>
```